Business Card Design

We are a commercial real estate brokerage in San Francisco, leasing office buildings downtown.
I would like a clean, elegant look. Simple but powerful .

Industry/Entity Type

Business

Contact Information for Business Card

Derek Holloway
lic# 07258143
415.555.0172
derek@velt-commercial.example
velt-commercial.example

```html
<!DOCTYPE html>
<html lang="en">
<head>
<meta charset="utf-8">
<title>VELT Commercial – Business Card</title>
<link href="https://fonts.googleapis.com/css2?family=Source+Sans+3:wght@400;600;700&display=swap" rel="stylesheet">
<style>
  :root {
    --slate: #7588a6;
    --slate-dark: #687c9c;
    --ink: #2b2b2b;
    --paper: #ffffff;
    --backdrop: #e9eaec;
  }
  * { margin: 0; padding: 0; box-sizing: border-box; }
  html, body {
    width: 1200px; height: 900px; overflow: hidden;
    background: var(--backdrop);
    font-family: "Source Sans 3", "Myriad Pro", Arial, sans-serif;
  }
  .card {
    position: absolute;
    border-radius: 16px;
    overflow: hidden;
    box-shadow: 0 6px 18px rgba(0,0,0,.12);
  }

  /* Front */
  .card--front {
    left: 78px; top: 35px; width: 588px; height: 362px;
    background: var(--paper);
  }
  .front-band {
    position: absolute; top: 28px; height: 99px;
    background: var(--slate);
  }
  .front-band--left { left: 0; width: 379px; }
  .front-band--right { left: 517px; right: 0; }
  .front-wordmark {
    position: absolute; right: 34px; top: 136px;
    text-align: center; color: var(--slate); font-weight: 700; line-height: 1;
  }
  .front-wordmark .wm-main { display: block; font-size: 66px; letter-spacing: 1px; }
  .front-wordmark .wm-sub { display: block; font-size: 29px; letter-spacing: .5px; margin-top: 2px; }

  .holder-name {
    position: absolute; left: 38px; top: 167px;
    font-size: 21px; font-weight: 600; color: var(--slate);
  }
  .contact-list {
    position: absolute; left: 37px; top: 217px; list-style: none;
    font-size: 16px; color: var(--ink);
  }
  .contact-list li { display: flex; align-items: center; height: 25px; }
  .contact-list svg { width: 13px; height: 13px; margin-right: 7px; fill: var(--slate); }
  .licence {
    position: absolute; left: 38px; top: 310px;
    font-size: 16px; font-weight: 600; color: var(--ink);
  }
  .licence .lic-label { color: var(--slate); margin-right: 4px; }

  /* Back */
  .card--back {
    left: 390px; top: 505px; width: 565px; height: 350px;
    background: var(--slate);
  }
  .back-band {
    position: absolute; top: 82px; height: 96px; background: var(--paper);
  }
  .back-band--left { left: 0; width: 200px; }
  .back-band--right { left: 365px; right: 0; }
  .back-wordmark {
    position: absolute; left: 0; right: 0; top: 196px;
    text-align: center; color: var(--paper); font-weight: 700; line-height: 1;
  }
  .back-wordmark .wm-main { display: block; font-size: 72px; letter-spacing: 1px; }
  .back-wordmark .wm-sub { display: block; font-size: 33px; letter-spacing: .5px; margin-top: 2px; }
</style>
</head>
<body>

<section class="card card--front" aria-label="Business card front">
  <div class="front-band front-band--left"></div>
  <div class="front-band front-band--right"></div>
  <div class="front-wordmark"><span class="wm-main">VELT</span><span class="wm-sub">COMMERCIAL</span></div>

  <p class="holder-name">Derek Holloway</p>
  <ul class="contact-list">
    <li><svg viewBox="0 0 24 24" aria-hidden="true"><path d="M6.6 10.8a15 15 0 0 0 6.6 6.6l2.2-2.2a1 1 0 0 1 1-.25 11.4 11.4 0 0 0 3.6.57 1 1 0 0 1 1 1V20a1 1 0 0 1-1 1A17 17 0 0 1 3 4a1 1 0 0 1 1-1h3.5a1 1 0 0 1 1 1c0 1.25.2 2.45.57 3.57a1 1 0 0 1-.25 1z"/></svg>415.555.0172</li>
    <li><svg viewBox="0 0 24 24" aria-hidden="true"><path d="M2 5h20v14H2z M3.5 6.5 12 13l8.5-6.5" fill="var(--slate)" stroke="#fff" stroke-width="1.5"/></svg>derek@velt-commercial.example</li>
    <li><svg viewBox="0 0 24 24" aria-hidden="true"><path d="M10 14a4 4 0 0 1 0-5.7l3-3a4 4 0 0 1 5.7 5.7l-1.5 1.5M14 10a4 4 0 0 1 0 5.7l-3 3A4 4 0 0 1 5.3 13l1.5-1.5" fill="none" stroke="var(--slate)" stroke-width="2.4" stroke-linecap="round"/></svg>velt-commercial.example</li>
  </ul>
  <p class="licence"><span class="lic-label">Lic#</span>07258143</p>
</section>

<section class="card card--back" aria-label="Business card back">
  <div class="back-band back-band--left"></div>
  <div class="back-band back-band--right"></div>
  <div class="back-wordmark"><span class="wm-main">VELT</span><span class="wm-sub">COMMERCIAL</span></div>
</section>

</body>
</html>
```